Investment company needing business card

We are wanting a business card which looks sharp and easy on the eye. We are thinking of having a business card with the logo embossed on it, to really make it stand out. We will only have a small amount of information of the business card, person's name, position, email address and phone number

Contact Information for Business Card

Danielle Frost
Executive Assistant
+64 21 473 5162
danielf@harwickpartners.co.nz

Requirements
Must have
• Embossed logo
Should not have
• Not to be busy

```html
<!DOCTYPE html>
<html lang="en">
<head>
<meta charset="utf-8">
<title>Harwick Partners – Business Card</title>
<link rel="stylesheet" href="https://fonts.googleapis.com/css2?family=Roboto+Condensed:wght@400;500&display=swap">
<style>
  :root {
    --backdrop: #e6e6e6;
    --card-light: #f1f1f1;
    --card-dark: #252525;
    --brand-green: #22b46e;
    --text-grey: #555555;
    --mark-grey: #8a8a8a;
    --mark-square: #1a1a1a;
  }
  * { margin: 0; padding: 0; box-sizing: border-box; }
  html, body { width: 1200px; height: 897px; overflow: hidden; }
  body {
    background: var(--backdrop);
    font-family: "Roboto Condensed", sans-serif;
    position: relative;
  }
  .card {
    position: absolute;
    left: 303px;
    width: 594px;
    height: 339px;
  }
  .card--front { top: 92px; background: var(--card-light); }
  .card--back { top: 469px; background: var(--card-dark); }

  .brand {
    position: absolute;
    display: flex;
    align-items: center;
    gap: 10px;
    white-space: nowrap;
  }
  .brand__square { display: block; }
  .brand__name {
    font-weight: 500;
    letter-spacing: 0.5px;
    text-transform: uppercase;
  }
  .card--front .brand { right: 35px; top: 40px; }
  .card--front .brand__square { width: 40px; height: 40px; background: var(--text-grey); }
  .card--front .brand__name { font-size: 30px; color: var(--brand-green); }

  .card--back .brand { left: 50%; top: 50%; transform: translate(-50%, -50%); gap: 14px; }
  .card--back .brand__square { width: 64px; height: 64px; background: var(--mark-square); }
  .card--back .brand__name { font-size: 42px; color: var(--mark-grey); }

  .person { position: absolute; left: 37px; top: 200px; }
  .person__name {
    font-size: 28px;
    font-weight: 400;
    color: var(--brand-green);
    text-transform: uppercase;
    line-height: 1;
  }
  .person__role { font-size: 15px; color: var(--text-grey); margin-top: 3px; }

  .divider {
    position: absolute;
    left: 37px;
    right: 36px;
    top: 265px;
    height: 1px;
    background: var(--brand-green);
  }
  .contact {
    position: absolute;
    left: 37px;
    right: 36px;
    top: 287px;
    display: flex;
    justify-content: space-between;
    font-size: 12.3px;
    color: var(--text-grey);
    list-style: none;
    white-space: nowrap;
  }
  .contact__label { color: var(--brand-green); }
  .contact__sep { color: var(--text-grey); }
</style>
</head>
<body>
  <section class="card card--front" aria-label="Business card front">
    <div class="brand">
      <span class="brand__square"></span>
      <span class="brand__name">Harwick Partners</span>
    </div>
    <div class="person">
      <h1 class="person__name">Danielle Frost</h1>
      <p class="person__role">Executive Assistant</p>
    </div>
    <div class="divider"></div>
    <ul class="contact">
      <li><span class="contact__label">P :</span> +64 21 473 5162</li>
      <li class="contact__sep">|</li>
      <li><span class="contact__label">E :</span> danielf@harwickpartners.co.nz</li>
      <li class="contact__sep">|</li>
      <li><span class="contact__label">W :</span> www.danielfharwickpartners.co.nz</li>
    </ul>
  </section>

  <section class="card card--back" aria-label="Business card back">
    <div class="brand">
      <span class="brand__square"></span>
      <span class="brand__name">Harwick Partners</span>
    </div>
  </section>
</body>
</html>
```